Modern Business Card for Larkwell 2018

Our company assumes the best about people. We are creating an online community of entrepreneurs and business leaders who struggle with marketing their business online.

This business card should POP! We recently got a new logo and are launching a new website next month, so our business cards should make a statement that feels:
-Fresh
-Smart
-Trustworthy
-Fun

Target Market(s)

small business owners, entrepreneurs

Industry/Entity Type

Digital Marketing

Contact Information for Business Card

Dimensions: 3.5" x 2"

Font styles to use
Sans Serif

Colors
f37122
ffffff

Requirements
Must have
• We need a business card with a modern, bold design. We will use one side of the card as a lead-generation offer, so text on one side will need to fit up to 140 characters. The business card should stick to our core colors (orange, black, and white).
Nice to have
• We think a vertical "portrait" design could be interesting.
Should not have
• Should not look like a traditional business card. The round icon should stand out from a distance.

```html
<!DOCTYPE html>
<html lang="en">
<head>
<meta charset="utf-8">
<title>Larkwell Business Card – Dana Morrow</title>
<link rel="stylesheet" href="https://fonts.googleapis.com/css2?family=Montserrat:wght@300;400;700;800&display=swap">
<style>
  :root {
    --brand-orange: #f37122;
    --paper: #ffffff;
  }
  * { margin: 0; padding: 0; box-sizing: border-box; }
  html, body {
    width: 775px;
    height: 1200px;
    overflow: hidden;
    background: var(--paper);
  }
  .card {
    position: relative;
    width: 775px;
    height: 1200px;
    background: var(--paper);
    font-family: "Montserrat", sans-serif;
  }
  .card__tab {
    position: absolute;
    left: 0;
    top: 0;
    width: 775px;
    height: 920px;
  }
  .card__role {
    position: absolute;
    top: 203px;
    left: 0;
    width: 775px;
    text-align: center;
    color: var(--paper);
    font-weight: 700;
    font-size: 21px;
    letter-spacing: 0.2px;
  }
  .card__name {
    position: absolute;
    top: 240px;
    left: 0;
    width: 775px;
    text-align: center;
    color: var(--paper);
    font-weight: 800;
    font-size: 52px;
    letter-spacing: 0.5px;
  }
  .card__brand {
    position: absolute;
    top: 660px;
    left: 0;
    width: 775px;
    text-align: center;
    color: var(--paper);
    font-weight: 800;
    font-size: 64px;
    line-height: 1;
  }
  .card__email {
    position: absolute;
    top: 1010px;
    left: 0;
    width: 775px;
    text-align: center;
    color: var(--brand-orange);
    font-weight: 300;
    font-size: 41px;
  }
</style>
</head>
<body>
  <main class="card">
    <svg class="card__tab" viewBox="0 0 775 920" aria-hidden="true">
      <path d="M130 0 H645 V662 A257.5 257.5 0 0 1 130 662 Z" fill="var(--brand-orange)"/>
    </svg>
    <p class="card__role">STORY MARKETING COACH</p>
    <h1 class="card__name">DANA MORROW</h1>
    <p class="card__brand">Larkwell</p>
    <p class="card__email">dana@larkwellnow.com</p>
  </main>
</body>
</html>
```